TORV Business Card Neil

Field Capital Advisory (TORV) is a consulting company that advises stakeholders in the Agricultural Industry. Based in rural NSW Australia, we need a good business card. TORV has a lifetime of agricultural experience and knowledge, particularly in the beef, wool and lamb markets. Though it is expanding into other rural ventures. Our clients are primarily off-farm investors who trust our business to advise on the best path forward for their agricultural investment. We also work with large players in the retail sector. Our image is trustworthy, reliable, smart and professional.
Updates

I think the black is too urban, perhaps a dark blue on one side and white on the other, or the yellow/orange on one side and white on the other??

we need to have the tag line "Customised Agribusiness Strategy" and our list of services:

"Due Diligence, Acquisition, Planning, Management, Strategy, Supply Chain" included in the design

we actually have 6 services - the should read in order:

Due diligence
Acquisition
Strategy
Planning 
Management
Supply chain

Target Market(s)

large rural land holders
senior players in agribusiness
senior management of retail food outlets
middle-senior aged men

Industry/Entity Type

Retail

Requirements
Must have
• high quality, 2 sides

logo

"Neil Ashcombe
Director
0413952617
neil@torv.com.au
PO Box 4721, Armidale NSW 2350"

tag line "Customised Agribusiness Strategy"

services provided

"Due diligence
Acquisition
Strategy
Planning
Management
Supply chain"
Should not have
• no images of animals or leaves

```html
<!DOCTYPE html>
<html lang="en">
<head>
<meta charset="utf-8">
<title>TORV Business Card – Neil Ashcombe</title>
<link rel="stylesheet" href="https://fonts.googleapis.com/css2?family=Cinzel:wght@400;500&family=EB+Garamond:wght@400;500&display=swap">
<style>
  :root {
    --backdrop: #4a4a4a;
    --card-white: #fdfdfc;
    --brand-blue: #2f5fae;
    --accent-orange: #f2a516;
    --accent-orange-deep: #e89410;
    --text-grey: #5d6066;
    --text-dark: #3b3d42;
    --yellow-light: #ece21c;
    --yellow-mid: #edc51a;
    --yellow-edge: #e9a913;
  }
  * { box-sizing: border-box; margin: 0; padding: 0; }
  html, body {
    width: 1200px;
    height: 1024px;
    overflow: hidden;
  }
  body {
    background: var(--backdrop);
    display: flex;
    flex-direction: column;
    align-items: center;
    justify-content: center;
    gap: 64px;
  }
  .card {
    position: relative;
    width: 700px;
    height: 400px;
    overflow: hidden;
    box-shadow: 0 12px 30px rgba(0,0,0,0.35);
  }

  /* ---------- Front ---------- */
  .card-front { background: var(--card-white); }
  .card-front .edge-band {
    position: absolute;
    left: 0; right: 0; bottom: 0;
    height: 26px;
    background: linear-gradient(90deg, var(--accent-orange), var(--accent-orange-deep));
  }
  .front-brand {
    position: absolute;
    left: 52px;
    top: 70px;
  }
  .brand-name {
    font-family: "Cinzel", serif;
    font-weight: 500;
    color: var(--brand-blue);
    line-height: 1;
    display: block;
  }
  .front-brand .brand-name { font-size: 64px; letter-spacing: 4px; }
  .brand-sub {
    font-family: "Cinzel", serif;
    font-weight: 500;
    color: var(--brand-blue);
    display: block;
  }
  .front-brand .brand-sub {
    font-size: 12.5px;
    letter-spacing: 1.2px;
    margin-top: 8px;
  }
  .rule-line {
    position: absolute;
    left: 52px;
    right: 318px;
    top: 197px;
    border-top: 2px dashed var(--accent-orange);
  }
  .person {
    position: absolute;
    left: 396px;
    top: 182px;
    white-space: nowrap;
  }
  .person-name {
    font-family: "Cinzel", serif;
    font-weight: 400;
    font-size: 23px;
    color: var(--accent-orange);
    letter-spacing: 1px;
    line-height: 1.1;
  }
  .person-role {
    font-family: "EB Garamond", serif;
    font-size: 17px;
    letter-spacing: 1.5px;
    color: var(--text-grey);
    margin-top: 4px;
  }
  .contact-list {
    position: absolute;
    left: 52px;
    top: 238px;
    list-style: none;
  }
  .contact-list li {
    display: flex;
    align-items: center;
    gap: 12px;
    font-family: "EB Garamond", serif;
    font-size: 17px;
    color: var(--text-dark);
    height: 30px;
  }
  .contact-icon { width: 15px; height: 15px; flex: none; }

  /* ---------- Back ---------- */
  .card-back {
    background: radial-gradient(ellipse at 50% 55%, var(--yellow-light) 0%, var(--yellow-mid) 55%, var(--yellow-edge) 100%);
  }
  .back-brand {
    position: absolute;
    left: 0; right: 0;
    top: 96px;
    text-align: center;
  }
  .back-brand .brand-name { font-size: 92px; letter-spacing: 8px; }
  .back-brand .brand-sub {
    font-size: 18px;
    letter-spacing: 2px;
    margin-top: 12px;
  }
  .tagline {
    font-family: "EB Garamond", serif;
    font-weight: 500;
    font-size: 20px;
    letter-spacing: 1px;
    color: var(--text-dark);
    margin-top: 14px;
  }
  .service-list {
    position: absolute;
    left: 0; right: 0;
    bottom: 34px;
    display: flex;
    justify-content: center;
    align-items: center;
    gap: 10px;
    list-style: none;
    font-family: "EB Garamond", serif;
    font-size: 16px;
    color: var(--brand-blue);
    letter-spacing: 0.5px;
  }
  .service-list li + li::before {
    content: "";
    display: inline-block;
    width: 5px;
    height: 5px;
    border-radius: 50%;
    background: var(--brand-blue);
    margin-right: 10px;
    vertical-align: middle;
  }
</style>
</head>
<body>

  <section class="card card-front" aria-label="Business card front">
    <div class="front-brand">
      <span class="brand-name">TORV</span>
      <span class="brand-sub">Field Capital Advisory</span>
    </div>

    <div class="rule-line"></div>

    <div class="person">
      <p class="person-name">Neil Ashcombe</p>
      <p class="person-role">DIRECTOR</p>
    </div>

    <ul class="contact-list">
      <li>
        <svg class="contact-icon" viewBox="0 0 16 16" aria-hidden="true">
          <rect x="4" y="1" width="8" height="14" rx="1.5" fill="none" stroke="var(--accent-orange)" stroke-width="1.6"/>
          <circle cx="8" cy="12.3" r="0.9" fill="var(--accent-orange)"/>
        </svg>
        0413 952 617
      </li>
      <li>
        <svg class="contact-icon" viewBox="0 0 16 16" aria-hidden="true">
          <rect x="1" y="3" width="14" height="10" rx="1" fill="none" stroke="var(--accent-orange)" stroke-width="1.6"/>
          <path d="M1.5 3.8 8 9l6.5-5.2" fill="none" stroke="var(--accent-orange)" stroke-width="1.6"/>
        </svg>
        neil@torv.com.au
      </li>
      <li>
        <svg class="contact-icon" viewBox="0 0 16 16" aria-hidden="true">
          <path d="M8 15s-5-5.2-5-8.8a5 5 0 0 1 10 0C13 9.8 8 15 8 15z" fill="var(--accent-orange)"/>
          <circle cx="8" cy="6.2" r="1.8" fill="var(--card-white)"/>
        </svg>
        PO Box 4721, Armidale NSW 2350
      </li>
    </ul>

    <div class="edge-band"></div>
  </section>

  <section class="card card-back" aria-label="Business card back">
    <div class="back-brand">
      <span class="brand-name">TORV</span>
      <span class="brand-sub">Field Capital Advisory</span>
      <p class="tagline">Customised Agribusiness Strategy</p>
    </div>
    <ul class="service-list">
      <li>Due diligence</li>
      <li>Acquisition</li>
      <li>Strategy</li>
      <li>Planning</li>
      <li>Management</li>
      <li>Supply chain</li>
    </ul>
  </section>

</body>
</html>
```